Design for the A4 Letterhead, envelope and A4 Folder

Design have to be clean, professional, unique (eye catchy) and high end.
Colors: Yellow (Code: 803C), Darker Grey and Black or white (optional)
Logo can be in white or black

Letterhead:
Contain: 1. Korvane Logo
2. Slogan "MADE WITH PRIDE"
3. Company information:
Korvane Valves Pte. Ltd. (Singapore)
Registration no: 201947215K
Tel: (65) 6418 2904
Fax: (65) 6472 9186
Email: sales@korvanevalves.example
Website: http://www.korvanevalves.example
4. Logo watermark

Envelope:
Contain: 1. Korvane Logo
3. website: http://www.korvanevalves.example and email address:
sales@korvanevalves.example
4. Logo watermark

Folder:
Contain: 1. Korvane Logo
3. Company's information:
Tel: (65) 6418 2904
Fax: (65) 6472 9186
4. QR Code
5. Logo watermark
6. On the inside there is a space to insert business card. Contrast colors
between the inside and cover.
Updates

For the Folder design, please be informed that we would prefer to have the Korvane logo on the left hand side of the cover page, rather than on the right hand side.And also if we could highlight the "Made with Pride" slogan with either the yellow box or black/grey box depending on the background color.For the Envelope design,it does not matter where the position of the logo is. But please also highlight the "Made with Pride" Slogan For the Letterhead design, the position of the logo must be on the left hand side and the slogan must be highlighted. In addition, please include the following company information (only for the letterhead design)Korvane Valves Pte. Ltd. (Singapore)Registration no: 200308878MTel: (65) 6535 3735Fax: (65) 6533 3570Email: sales@dynatechpumps.comWebsite: http://www.korvanevalves.example Added Wednesday, August 2, 2017

Target Market(s)

Business to Business, High End market

Industry/Entity Type

It Professional

Font styles to use
Serif

Requirements
Must have
• Design have to be clean, professional, unique (eye catchy) and high end.
Nice to have
• color contrast but still maintaining the professionalism and the seriousness
Should not have
• Messy look, futuristic look, too crowded

```html
<!DOCTYPE html>
<html lang="en">
<head>
<meta charset="utf-8">
<title>Korvane Valves Letterhead</title>
<link rel="stylesheet" href="https://fonts.googleapis.com/css2?family=Open+Sans:wght@400;700&family=Saira+Semi+Condensed:wght@400;600&display=swap">
<style>
  :root {
    --backdrop: #e9df8a;
    --paper: #ffffff;
    --brand-yellow: #f5e52a;
    --dark-grey: #3c3c3e;
    --mid-grey: #6b6b6d;
    --ink: #1a1a1a;
    --watermark: #f1f1f1;
  }
  * { box-sizing: border-box; margin: 0; padding: 0; }
  html, body { width: 1200px; height: 784px; overflow: hidden; }
  body {
    background: var(--backdrop);
    font-family: "Open Sans", sans-serif;
    position: relative;
  }
  .letterhead {
    position: absolute;
    left: 338px; top: 22px;
    width: 524px; height: 740px;
    background: var(--paper);
    box-shadow: 0 6px 18px rgba(0,0,0,.12);
    overflow: hidden;
  }
  .corner-mark { position: absolute; height: 5px; }
  .corner-mark--top-dark { top: 0; left: 34px; width: 34px; background: var(--dark-grey); }
  .corner-mark--top-yellow { top: 0; left: 68px; width: 30px; background: var(--brand-yellow); }
  .corner-mark--side { right: 0; width: 5px; }
  .corner-mark--side-dark { top: 40px; height: 40px; background: var(--dark-grey); right: 0; width: 5px; position: absolute; }
  .corner-mark--side-yellow { top: 0; height: 40px; background: var(--brand-yellow); right: 0; width: 5px; position: absolute; }

  .brand {
    position: absolute;
    left: 64px; top: 120px;
    display: flex; align-items: center; gap: 8px;
  }
  .brand__dot {
    width: 26px; height: 26px; border-radius: 50%;
    border: 3px solid var(--ink);
  }
  .brand__name {
    font-family: "Saira Semi Condensed", sans-serif;
    font-weight: 600; font-size: 22px; letter-spacing: 1px;
    color: var(--ink);
  }

  .watermark {
    position: absolute;
    left: 60px; top: 360px;
    width: 270px; height: 270px;
  }

  .footer {
    position: absolute; left: 0; right: 0; bottom: 0; height: 110px;
  }
  .footer__slogan {
    position: absolute; left: 200px; top: 0;
    font-family: "Saira Semi Condensed", sans-serif;
    font-size: 24px; font-weight: 400; letter-spacing: .5px;
    color: var(--brand-yellow);
  }
  .footer__company {
    position: absolute; left: 196px; top: 34px;
    font-size: 9px; font-weight: 700; color: var(--ink);
  }
  .footer__contacts {
    position: absolute; left: 14px; right: 10px; top: 66px;
    display: flex; gap: 7px; white-space: nowrap;
    font-size: 8.4px; color: var(--mid-grey);
  }
  .footer__contacts span { display: inline-flex; align-items: center; gap: 3px; }
  .footer__contacts i {
    width: 6px; height: 6px; border-radius: 50%; background: var(--dark-grey); display: inline-block;
  }
  .footer__band { position: absolute; left: 0; bottom: 0; width: 100%; height: 16px; }
</style>
</head>
<body>
  <main class="letterhead">
    <div class="corner-mark corner-mark--top-dark"></div>
    <div class="corner-mark corner-mark--top-yellow"></div>
    <div class="corner-mark--side-yellow"></div>
    <div class="corner-mark--side-dark"></div>

    <header class="brand">
      <span class="brand__dot"></span>
      <span class="brand__name">KORVANE</span>
    </header>

    <svg class="watermark" viewBox="0 0 270 270" aria-hidden="true">
      <circle cx="135" cy="135" r="125" fill="none" stroke="var(--watermark)" stroke-width="22"/>
      <text x="135" y="146" text-anchor="middle" font-family="Saira Semi Condensed, sans-serif" font-weight="600" font-size="34" fill="var(--watermark)">KORVANE</text>
    </svg>

    <footer class="footer">
      <div class="footer__slogan">MADE WITH PRIDE</div>
      <div class="footer__company">Korvane Valves Pte. Ltd. (Singapore)</div>
      <div class="footer__contacts">
        <span><i></i>(65) 6418 2904</span>
        <span><i></i>(65) 6472 9186</span>
        <span><i></i>sales@korvanevalves.example</span>
        <span><i></i>www.korvanevalves.example</span>
        <span><i></i>Regd. No: 201947215K</span>
      </div>
      <svg class="footer__band" viewBox="0 0 524 16" preserveAspectRatio="none" aria-hidden="true">
        <rect x="0" y="8" width="524" height="8" fill="var(--dark-grey)"/>
        <polygon points="150,8 160,0 340,0 350,8 340,16 160,16" fill="var(--brand-yellow)"/>
        <rect x="0" y="14" width="524" height="2" fill="var(--ink)"/>
      </svg>
    </footer>
  </main>
</body>
</html>
```